Business Card Design

New business card design

Target Market(s)

Residential & Commercial Property Managers

Industry/Entity Type

Plumbing Services

Contact Information for Business Card

Name - Rowan Keddle, title - Director, Phone Number - 0431 286 517, email - rowan@tbk-plumbing.com.au, Company ABN - 73 215 904 386,

Font styles to use
Sans Serif

Colors
0054AA
0677BA
7BADD7
CADEEF
E8F1F8

```html
<!DOCTYPE html>
<html lang="en">
<head>
<meta charset="utf-8">
<title>TBK Plumbing Services – Business Card</title>
<link rel="stylesheet" href="https://fonts.googleapis.com/css2?family=Lato:wght@400;700&display=swap">
<style>
  :root {
    --stage: #9a9b9f;
    --card-light: #f7f7f8;
    --card-dark: #262c33;
    --card-dark-edge: #1b2026;
    --ink: #2b3138;
    --ink-soft: #6d7278;
    --accent: #1f9bd7;
    --pipe: #e4e5e7;
    --rule: #2b3138;
    --on-dark: #ffffff;
  }
  * { box-sizing: border-box; margin: 0; padding: 0; }
  html, body {
    width: 1200px; height: 960px; overflow: hidden;
    background: var(--stage);
    font-family: "Lato", "Helvetica Neue", Arial, sans-serif;
  }
  .stage {
    position: relative; width: 1200px; height: 960px;
    background: radial-gradient(ellipse at 40% 45%, #b9babd 0%, var(--stage) 70%);
  }
  .card {
    position: absolute; left: 250px; width: 700px; height: 400px;
    box-shadow: 0 10px 24px rgba(0,0,0,.28);
    overflow: hidden;
  }
  /* back of card */
  .card--back { top: 50px; background: var(--card-dark); }
  .card__pattern {
    position: absolute; inset: 0;
    background: linear-gradient(135deg, #343c45 0%, var(--card-dark) 55%, var(--card-dark-edge) 100%);
  }
  .brand {
    position: absolute; display: flex; align-items: center; gap: 14px;
    font-weight: 400; white-space: nowrap;
  }
  .brand__dot { width: 18px; height: 18px; border-radius: 50%; background: var(--accent); flex: none; }
  .brand__name { font-size: 40px; letter-spacing: 2px; }
  .card--back .brand { left: 50%; top: 50%; transform: translate(-50%, -50%); color: var(--on-dark); }
  /* front of card */
  .card--front { top: 500px; background: var(--card-light); }
  .card__pipe {
    position: absolute; left: 150px; top: 0; width: 10px; height: 120px;
    background: var(--pipe); border-radius: 0 0 2px 2px;
  }
  .person { position: absolute; left: 42px; top: 140px; }
  .person__name { font-weight: 700; font-size: 34px; color: var(--accent); line-height: 1.1; }
  .person__role { font-size: 22px; color: var(--ink); margin-top: 2px; }
  .card--front .brand { right: 50px; top: 110px; color: var(--ink); }
  .brand--front .brand__name { font-size: 34px; }
  .card__rule {
    position: absolute; left: 220px; right: 0; top: 258px; height: 2px; background: var(--rule);
  }
  .contact {
    position: absolute; right: 34px; top: 280px; list-style: none;
    font-size: 22px; color: var(--ink); text-align: right;
  }
  .contact li { display: flex; align-items: center; justify-content: flex-end; gap: 12px; height: 34px; }
  .contact svg { width: 20px; height: 20px; fill: var(--accent); flex: none; }
</style>
</head>
<body>
<main class="stage">
  <section class="card card--back" aria-label="Card back">
    <div class="card__pattern" role="img" aria-label="Dark background with a subtle repeating water drop pattern"></div>
    <div class="brand">
      <span class="brand__dot"></span>
      <span class="brand__name">tbk plumbing services</span>
    </div>
  </section>

  <section class="card card--front" aria-label="Card front">
    <div class="card__pipe"></div>
    <div class="person">
      <p class="person__name">Rowan Keddle</p>
      <p class="person__role">Director</p>
    </div>
    <div class="brand brand--front">
      <span class="brand__dot"></span>
      <span class="brand__name">tbk plumbing services</span>
    </div>
    <div class="card__rule"></div>
    <ul class="contact">
      <li>0431 286 517
        <svg viewBox="0 0 24 24" aria-hidden="true"><path d="M6.6 10.8a15 15 0 0 0 6.6 6.6l2.2-2.2c.3-.3.7-.4 1-.2 1.1.4 2.3.6 3.6.6.6 0 1 .4 1 1V20c0 .6-.4 1-1 1A17 17 0 0 1 3 4c0-.6.4-1 1-1h3.5c.6 0 1 .4 1 1 0 1.3.2 2.5.6 3.6.1.3 0 .7-.2 1z"/></svg>
      </li>
      <li>rowan@tbk-plumbing.com.au
        <svg viewBox="0 0 24 24" aria-hidden="true"><path d="M2 5h20v14H2zm2 2v.4l8 5 8-5V7zm0 2.8V17h16V9.8l-8 5z"/></svg>
      </li>
      <li>ABN - 73 215 904 386
        <svg viewBox="0 0 24 24" aria-hidden="true"><circle cx="12" cy="12" r="10"/><path d="M2 12h20M12 2c3 3 3 17 0 20M12 2c-3 3-3 17 0 20" stroke="#f7f7f8" stroke-width="1.4" fill="none"/></svg>
      </li>
    </ul>
  </section>
</main>
</body>
</html>
```